Quorbelline.io - Please redesign to make it look better from current design

We already have the current website, that you can access but we think it can improve from current version.
Quorbelline is a cryptocurrency hedge fund that allow you to participate in the hedge fund with cryptocurrency such as eth.
At current phase, we are doing an ICO, then we want to make sure that the website it looks professional, beautiful and trustable enough for investors after looking at our website.
Target Market(s)
Investors
Industry/Entity Type
Investment
Coding
Coded - Design and coding required
Number of Pages Required
1 page
Look and feel
Each slider illustrates characteristics of the customer's brand and the style your logo design should communicate.

```html
<!DOCTYPE html>
<html lang="en">
<head>
<meta charset="utf-8">
<title>Quorbelline – Digital Asset Management</title>
<link href="https://fonts.googleapis.com/css2?family=Mulish:wght@400;600;700;800&display=swap" rel="stylesheet">
<style>
:root{
  --navy:#0d2f6e;
  --navy-deep:#081f52;
  --ink:#122a57;
  --text:#2b3345;
  --muted:#6a7285;
  --accent:#3a9ad6;
  --team-band:#3d9fd8;
  --soft:#e6eaf1;
  --footer:#e9edf3;
  --line:#cfd4dc;
  --white:#ffffff;
}
*{margin:0;padding:0;box-sizing:border-box}
html,body{width:1200px;height:3448px;overflow:hidden;background:var(--white)}
body{position:relative;font-family:"Mulish",Arial,sans-serif;color:var(--text)}
.abs{position:absolute}
.btn{position:absolute;display:flex;align-items:center;justify-content:center;background:var(--accent);color:var(--white);font-size:13px;font-weight:600;text-decoration:none}
.brand{display:flex;align-items:center;gap:10px;font-weight:800;color:var(--navy)}
.brand-dot{border-radius:50%;background:currentColor;display:block}

/* hero */
.hero{position:absolute;left:0;top:0;width:1200px;height:592px;background:radial-gradient(ellipse at 70% 45%,#1a4795 0%,var(--navy) 45%,var(--navy-deep) 100%)}
.hero .brand{position:absolute;left:88px;top:30px;color:var(--white);font-size:26px}
.nav{position:absolute;right:87px;top:62px;display:flex;gap:52px;font-size:14px;color:var(--white)}
.hero-rule{position:absolute;left:520px;right:87px;top:141px;height:1px;background:rgba(255,255,255,.25)}
.hero h1{position:absolute;left:88px;top:234px;font-size:70px;font-weight:800;color:var(--white)}
.hero h2{position:absolute;left:88px;top:325px;font-size:32px;font-weight:600;color:var(--white)}
.hero .btn{left:88px;top:376px;width:120px;height:40px}
.dots{position:absolute;left:90px;top:444px;display:flex;gap:6px}
.dots span{width:16px;height:16px;border-radius:50%;border:2px solid var(--white)}
.dots span.on{background:var(--accent);border-color:var(--accent)}
.hero-art{position:absolute;left:720px;top:150px;width:340px;height:420px;border-radius:24px;background:linear-gradient(160deg,rgba(255,255,255,.14),rgba(58,154,214,.18))}

/* sections */
.center-mark{position:absolute;left:0;width:1200px;display:flex;justify-content:center}
.center-mark .brand{font-size:28px}
.sec-title{position:absolute;left:0;width:1200px;text-align:center;font-size:40px;font-weight:700;color:var(--ink)}
.sec-title b{color:var(--navy);font-weight:800}
.welcome-copy{position:absolute;left:180px;width:840px;top:804px;text-align:center;font-size:12.5px;line-height:1.75;color:var(--text)}
.rule{position:absolute;left:87px;width:1026px;height:1px;background:var(--line)}
.feature h3{position:absolute;font-size:40px;font-weight:700;color:var(--ink)}
.feature p{position:absolute;font-size:12.5px;line-height:1.8;color:var(--text)}
.art{position:absolute;border-radius:50%;background:var(--soft)}

/* team */
.team{position:absolute;left:0;top:1985px;width:1200px;height:647px;background:linear-gradient(180deg,#4aa7dd,var(--team-band))}
.team .brand{color:var(--navy)}
.team-card{position:absolute;top:218px;width:298px;height:361px;background:var(--white)}
.team-photo{width:298px;height:278px;background:linear-gradient(180deg,#8b7a6c,#4f4640)}
.team-card h4{text-align:center;margin-top:16px;font-size:19px;font-weight:600;color:var(--ink)}
.team-card span{display:block;text-align:center;font-size:12px;font-weight:600;color:var(--ink);margin-top:4px}

/* cta */
.cta .btn{left:474px;top:2882px;width:252px;height:44px;font-size:15px;box-shadow:0 4px 8px rgba(0,0,0,.2)}

/* footer */
.footer{position:absolute;left:0;top:3040px;width:1200px;height:320px;background:var(--footer);overflow:hidden}
.footer h5{position:absolute;font-size:17px;font-weight:600;color:var(--navy)}
.contact{position:absolute;left:88px;font-size:12px;line-height:1.6;color:var(--muted);display:flex;gap:20px}
.contact svg{flex:none;margin-top:3px}
.links{position:absolute;top:127px;font-size:12px;line-height:2.2;color:var(--muted);list-style:none}
.subscribe{position:absolute;left:790px;top:180px;display:flex}
.subscribe .field{width:214px;height:44px;background:var(--white);font-size:11px;color:var(--muted);display:flex;align-items:center;padding-left:14px}
.subscribe .go{width:106px;height:44px;background:var(--accent);color:var(--white);font-weight:700;font-size:15px;display:flex;align-items:center;justify-content:center}
.socials{position:absolute;left:968px;top:242px;display:flex;gap:7px}
.socials span{width:22px;height:22px;border-radius:50%}
.copyright{position:absolute;left:0;top:3404px;width:1200px;text-align:center;font-size:13px;color:var(--muted)}
</style>
</head>
<body>

<header class="hero">
  <div class="brand"><span class="brand-dot" style="width:22px;height:22px"></span>Quorbelline</div>
  <nav class="nav"><span>Home</span><span>About Us</span><span>Services</span><span>Blog</span><span>Team</span><span>Contact Us</span></nav>
  <div class="hero-rule"></div>
  <h1>Quorbelline</h1>
  <h2>Digital Asset Management</h2>
  <a class="btn" href="#">Read More &gt;&gt;</a>
  <div class="dots"><span></span><span class="on"></span><span></span></div>
  <div class="hero-art" role="img" aria-label="Illustration of a businessman beside stacks of money and coins with rising arrows"></div>
</header>

<section class="welcome">
  <div class="center-mark" style="top:662px"><div class="brand"><span class="brand-dot" style="width:18px;height:18px"></span>Quorbelline</div></div>
  <h2 class="sec-title" style="top:732px">Welcome to <b>Quorbelline</b></h2>
  <p class="welcome-copy">Sed ut perspiciatis unde omnis iste natus error sit voluptatem accusantium doloremque laudantium, totam rem aperiam, eaque ipsa quae ab illo inventore veritatis et quasi architecto beatae vitae dicta sunt explicabo. Nemo enim ipsam voluptatem quia voluptas sit aspernatur aut odit aut fugit, sed quia consequuntur magni dolores eos qui ratione voluptatem sequi nesciunt. Neque porro quisquam est, qui dolorem ipsum quia dolor sit amet, consectetur, adipisci velit, sed quia non numquam eius modi tempora incidunt ut labore et dolore magnam aliquam quaerat voluptatem. Ut enim ad minima veniam,</p>
  <a class="btn" href="#" style="left:540px;top:928px;width:120px;height:40px">Read More &gt;&gt;</a>
</section>

<div class="rule" style="top:1077px"></div>

<section class="feature">
  <h3 style="left:87px;top:1188px">Definition</h3>
  <p style="left:87px;top:1256px;width:550px">Quorbelline process and manages on hedge fund strategy models which invests in a diversified portfolio of blockchain tokens. Blockchain tokens are emerging which add a monetary incentive layer to p2p protocols and facilitate equity crowdfunding that anyone in the world can participate in.</p>
  <a class="btn" href="#" style="left:87px;top:1352px;width:120px;height:40px">Read More &gt;&gt;</a>
  <div class="art" role="img" aria-label="Illustration of a presenter showing charts to an audience" style="left:698px;top:1152px;width:290px;height:290px"></div>
</section>

<div class="rule" style="top:1510px"></div>

<section class="feature">
  <div class="art" role="img" aria-label="Illustration of a light bulb with gears" style="left:87px;top:1585px;width:265px;height:265px"></div>
  <h3 style="left:575px;top:1622px">Process</h3>
  <p style="left:575px;top:1690px;width:540px">Hedge Fund Model<br>Quorbelline run on closed-end fund (CEF) model which offers its shares to investors and utilize the fund to speculate and invest in the innovative blockchain tokens. Quorbelline will charge an upfront annual operation fee 4% of the money raised during the ICO. After</p>
  <a class="btn" href="#" style="left:575px;top:1785px;width:120px;height:40px">Read More &gt;&gt;</a>
</section>

<section class="team">
  <div class="center-mark" style="top:66px"><div class="brand"><span class="brand-dot" style="width:18px;height:18px"></span>Quorbelline</div></div>
  <h2 class="sec-title" style="top:136px;font-weight:600;color:var(--navy)">Executive Team</h2>
  <div class="team-card" style="left:117px"><div class="team-photo" role="img" aria-label="Portrait photo of the director"></div><h4>Dorian Vattelmark</h4><span>Director</span></div>
  <div class="team-card" style="left:451px"><div class="team-photo" role="img" aria-label="Portrait photo of the technical advisor" style="background:linear-gradient(180deg,#d9d5c4,#b8b2a0)"></div><h4 style="font-weight:800">Kestrel Obanweyo</h4><span>Technical advisor</span></div>
  <div class="team-card" style="left:785px"><div class="team-photo" role="img" aria-label="Portrait photo of the marketing consultant" style="background:linear-gradient(180deg,#7a3a22,#4a2414)"></div><h4>Lucan Ferreira-Holt</h4><span>Marketing Consultant</span></div>
</section>

<section class="cta">
  <div class="center-mark" style="top:2725px"><div class="brand"><span class="brand-dot" style="width:18px;height:18px"></span>Quorbelline</div></div>
  <h2 class="sec-title" style="top:2796px;font-weight:600;color:var(--navy)">For More Information</h2>
  <a class="btn" href="#">DOWNLOAD WHITEPAPER</a>
</section>

<footer class="footer">
  <h5 style="left:87px;top:74px">QUICK CONTACT</h5>
  <div class="contact" style="top:125px;width:330px">
    <svg width="10" height="12" viewBox="0 0 10 12"><path d="M5 0a4 4 0 0 0-4 4c0 3 4 8 4 8s4-5 4-8a4 4 0 0 0-4-4zm0 5.5A1.5 1.5 0 1 1 5 2.5a1.5 1.5 0 0 1 0 3z" fill="#6a7285"/></svg>
    <span>Suite 08-12, 9B/F, East Wing, Meridian Trade Plaza, Riverside Quay, 42, Lantern Road, Harbourview District, Port Alden.</span>
  </div>
  <div class="contact" style="top:215px">
    <svg width="11" height="11" viewBox="0 0 11 11"><path d="M2 0l2 2.5-1.2 1.3a7 7 0 0 0 4.4 4.4L8.5 7 11 9l-1.5 2C4.5 11 0 6.5 0 1.5z" fill="#6a7285"/></svg>
    <span>555-014-2290</span>
  </div>
  <div class="contact" style="top:250px">
    <svg width="12" height="9" viewBox="0 0 12 9"><rect width="12" height="9" fill="#6a7285"/><path d="M0 0l6 5 6-5" stroke="#e9edf3" fill="none"/></svg>
    <span>info@quorbelline.io</span>
  </div>
  <h5 style="left:490px;top:74px">INFO</h5>
  <ul class="links" style="left:490px"><li>&gt; Home</li><li>&gt; About Us</li><li>&gt; Services</li></ul>
  <ul class="links" style="left:592px"><li>&gt; Team</li><li>&gt; Contact Us</li><li>&gt; Blog</li></ul>
  <div class="brand abs" style="left:958px;top:112px;font-size:26px"><span class="brand-dot" style="width:22px;height:22px"></span>Quorbelline</div>
  <div class="subscribe"><div class="field">Enter your email</div><div class="go">SIGN UP</div></div>
  <div class="socials">
    <span style="background:#3b5998"></span><span style="background:#3ea6e3"></span><span style="background:#dc4a38"></span><span style="background:#cc2020"></span><span style="background:#c13584"></span>
  </div>
</footer>

<p class="copyright">Copyright (c) 2017. Quorbelline. All rights reserved.</p>

</body>
</html>
```